Business Card Design Project

We are not a new company, but renamed to "Vantorin Kitchens" last year. We specialize in modern high-end cabinetry imports. We would like to communicate a sense of quality and cutting edge technology. Ideally the design would incorporate our logo colors, silver, red and preferably a black, matte background. Though we are open to suggestions.
Logo is attached.
Edit: I have attached rough drafts of the previous cards, this way you will have all necessary content that needs to go on the cards.
Updates
Project Deadline Extended
Reason: We have received a lot of great designs, but due to the sheer number we couldn't respond to all. We will extend the deadline for another 7 days to finalize and provide feedback to designers.
Thank you for your hard work!
Industry/Entity Type
Business
Look and feel
Each slider illustrates characteristics of the customer's brand and the style your logo design should communicate.

```html
<!DOCTYPE html>
<html lang="en">
<head>
<meta charset="utf-8">
<title>Vantorin Kitchens — Business Card</title>
<link rel="stylesheet" href="https://fonts.googleapis.com/css2?family=Arimo:wght@400;700&display=swap">
<style>
  :root {
    --bg: #e4e3ea;
    --card-black: #0e0e0f;
    --card-charcoal: #2a2a2c;
    --silver: #c9c9cc;
    --silver-light: #e6e6e8;
    --grey-band: #a9a9ab;
    --red: #e3161d;
    --white: #ffffff;
    --ink-dark: #1a1a1a;
  }
  * { box-sizing: border-box; margin: 0; padding: 0; }
  html, body { width: 1200px; height: 987px; overflow: hidden; }
  body {
    background: var(--bg);
    font-family: "Arimo", Arial, sans-serif;
    position: relative;
  }
  .card {
    position: absolute;
    left: 250px;
    width: 700px;
    height: 400px;
    border-radius: 28px;
    overflow: hidden;
    background:
      repeating-linear-gradient(90deg, rgba(255,255,255,0.018) 0 1px, transparent 1px 3px),
      radial-gradient(ellipse at 60% 35%, var(--card-charcoal) 0%, var(--card-black) 70%);
    box-shadow: 0 10px 24px rgba(0,0,0,0.18);
  }
  .card--front { top: 70px; }
  .card--back { top: 517px; }

  .card__swoosh { position: absolute; inset: 0; width: 100%; height: 100%; }

  .brand {
    position: absolute;
    display: flex;
    align-items: center;
    gap: 14px;
    color: var(--silver);
    font-weight: 700;
    text-transform: uppercase;
    letter-spacing: 2px;
  }
  .brand__mark {
    width: 22px; height: 22px;
    background: var(--silver);
  }
  .card--front .brand { left: 190px; top: 74px; font-size: 38px; }
  .card--back .brand {
    left: 0; right: 0; top: 0; bottom: 0;
    justify-content: center;
    font-size: 50px;
  }
  .card--back .brand__mark { width: 28px; height: 28px; }

  .contact {
    position: absolute;
    left: 190px;
    top: 150px;
    color: var(--white);
  }
  .contact__name { font-size: 20px; font-weight: 700; text-transform: uppercase; margin-bottom: 14px; }
  .contact__role { font-weight: 400; text-transform: none; }
  .contact__line {
    display: flex; align-items: center; gap: 9px;
    font-size: 17px; margin-bottom: 9px;
  }
  .contact__line svg { width: 15px; height: 15px; fill: var(--red); flex: none; }
  .contact__gap { width: 18px; }

  .address {
    position: absolute;
    right: 48px;
    bottom: 30px;
    text-align: right;
    color: var(--ink-dark);
    font-size: 19px;
    line-height: 1.3;
  }
</style>
</head>
<body>
  <section class="card card--front">
    <svg class="card__swoosh" viewBox="0 0 700 400" preserveAspectRatio="none" aria-hidden="true">
      <path d="M0 120 C 60 250, 200 330, 700 300 L700 400 L0 400 Z" fill="var(--grey-band)"/>
      <path d="M0 120 C 60 250, 200 330, 700 300" fill="none" stroke="var(--red)" stroke-width="5"/>
      <path d="M0 112 C 70 240, 220 318, 700 288" fill="none" stroke="var(--card-black)" stroke-width="6"/>
    </svg>

    <div class="brand"><span class="brand__mark"></span>Vantorin Kitchens</div>

    <div class="contact">
      <p class="contact__name">Marcus Delane, <span class="contact__role">Director</span></p>
      <p class="contact__line">
        <svg viewBox="0 0 16 16"><path d="M3 1h3l1.5 4-2 1.3a9 9 0 0 0 4.2 4.2L11 8.5l4 1.5v3a2 2 0 0 1-2 2A12 12 0 0 1 1 3a2 2 0 0 1 2-2z"/></svg>
        780.555.0142
      </p>
      <p class="contact__line">
        <svg viewBox="0 0 16 16"><path d="M2 5h12v8H2zM4 3h8v2H4zM4 8h8v1H4z"/></svg>
        780.555.0187
        <span class="contact__gap"></span>
        <svg viewBox="0 0 16 16"><path d="M5 1h6a1 1 0 0 1 1 1v12a1 1 0 0 1-1 1H5a1 1 0 0 1-1-1V2a1 1 0 0 1 1-1zm0 2v9h6V3z"/></svg>
        780.555.0163
      </p>
      <p class="contact__line">
        <svg viewBox="0 0 16 16"><path d="M1 3h14v10H1zm1.5 1.2V5l5.5 4 5.5-4v-.8L8 8z"/></svg>
        marcus@vantorinkitchens.ca
      </p>
    </div>

    <p class="address">1820 - 84 St.<br>Edmonton, AB T5X 2K9</p>
  </section>

  <section class="card card--back">
    <div class="brand"><span class="brand__mark"></span>Vantorin Kitchens</div>
  </section>
</body>
</html>
```